Orvane Mechanical - Letterhead

We are a plumbing and hvac company based in Calgary. This letterhead will be on our quotes, invoices, preventative maintenance proposals etc.

```html
<!DOCTYPE html>
<html lang="en">
<head>
<meta charset="utf-8">
<title>Orvane Mechanical – Letterhead</title>
<link rel="stylesheet" href="https://fonts.googleapis.com/css2?family=Lato:wght@400;700&family=Satisfy&display=swap">
<style>
  :root {
    --backdrop: #c9c9c9;
    --paper: #ffffff;
    --ink: #4a4a4a;
    --ink-strong: #3a3a3a;
    --brand-blue: #1f67ad;
    --brand-orange: #e0561c;
  }
  * { box-sizing: border-box; margin: 0; padding: 0; }
  html, body { width: 1200px; height: 1159px; overflow: hidden; }
  body {
    background: var(--backdrop);
    font-family: "Lato", sans-serif;
    color: var(--ink);
    position: relative;
  }
  .letterhead {
    position: absolute;
    left: 211px; top: 30px;
    width: 778px; height: 1100px;
    background: var(--paper);
    box-shadow: 0 10px 30px rgba(0,0,0,.25);
  }
  .brand {
    position: absolute; left: 70px; top: 78px;
    display: flex; align-items: center; gap: 10px;
  }
  .brand-dot { width: 16px; height: 16px; border-radius: 50%; background: var(--brand-orange); }
  .brand-name {
    font-weight: 700; font-size: 26px; color: var(--brand-blue);
    letter-spacing: .5px;
  }
  .contact {
    position: absolute; left: 448px; top: 50px;
    border-left: 2px solid var(--brand-orange);
    padding: 4px 0 6px 16px;
    font-size: 13px; line-height: 17px; color: var(--ink-strong);
  }
  .contact-address { margin-bottom: 4px; }
  .contact-line { display: flex; align-items: center; gap: 8px; }
  .contact-line svg { width: 11px; height: 11px; fill: var(--brand-orange); flex: none; }
  .letter-body {
    position: absolute; left: 88px; top: 300px; width: 600px;
    font-size: 13.5px; line-height: 18px;
  }
  .date { margin-bottom: 18px; }
  .recipient { margin-left: 12px; margin-bottom: 14px; }
  .recipient p + p { margin-top: 12px; }
  .greeting { margin-left: 24px; font-weight: 700; font-size: 17px; color: var(--ink-strong); margin-bottom: 12px; }
  .paragraph { margin-left: 24px; margin-bottom: 18px; }
  .closing { margin-left: 150px; margin-top: 42px; }
  .signature {
    font-family: "Satisfy", cursive; font-size: 36px;
    color: var(--ink-strong); margin-top: 8px; margin-left: 10px;
  }
  .footer-band {
    position: absolute; left: 0; right: 0; bottom: 0; height: 12px;
    display: flex;
  }
  .footer-band .band-orange { width: 270px; background: var(--brand-orange); }
  .footer-band .band-gap { width: 5px; background: var(--paper); }
  .footer-band .band-blue { flex: 1; background: var(--brand-blue); }
</style>
</head>
<body>
  <main class="letterhead">
    <header>
      <div class="brand">
        <span class="brand-dot"></span>
        <span class="brand-name">Orvane Mechanical</span>
      </div>
      <address class="contact" style="font-style:normal">
        <div class="contact-address">410 Ridgeway Avenue #200<br>Calgary, AB T2P 1J9</div>
        <div class="contact-line">
          <svg viewBox="0 0 12 12" aria-hidden="true"><path d="M1 4c0-2 2-3 5-3s5 1 5 3v1H8V4H4v1H1z M3 6h6l1 5H2z"/></svg>
          <span>877-555-0148</span>
        </div>
        <div class="contact-line">
          <svg viewBox="0 0 12 12" aria-hidden="true"><path d="M0 2h12v8H0z M0 2l6 5 6-5" stroke="#fff" stroke-width="1"/></svg>
          <span>info@orvanemechanical.com</span>
        </div>
        <div class="contact-line">
          <svg viewBox="0 0 12 12" aria-hidden="true"><circle cx="6" cy="6" r="6"/><path d="M0 6h12M6 0v12" stroke="#fff" stroke-width="1"/></svg>
          <span>www.orvanemechanical.com</span>
        </div>
      </address>
    </header>

    <section class="letter-body">
      <p class="date">June -22-2020</p>
      <div class="recipient">
        <p>Mr, John Doe<br>President</p>
        <p>Link Corporation<br>123 Street Name, Suite# 10<br>City, State, 120023</p>
      </div>
      <p class="greeting">Dear Mr, John</p>
      <p class="paragraph">Lorem ipsum dolor sit amet, consectetur adipisicing elit, sed do eiusmod tempor incididunt ut labore et dolore magna aliqua. Ut enim ad minim veniam, quis nostrud exercitation ullamco laboris nisi ut aliquip ex ea commodo consequat. Duis aute irure dolor in reprehenderit in voluptate velit esse cillum dolore eu fugiat nulla pariatur.</p>
      <p class="paragraph">Lorem ipsum dolor sit amet, consectetur adipisicing elit, sed do eiusmod tempor incididunt ut labore et dolore magna aliqua. Ut enim ad minim veniam, quis nostrud exercitation ullamco laboris nisi ut aliquip ex ea commodo consequat. Duis aute irure dolor in reprehenderit in voluptate velit esse cillum dolore eu fugiat nulla pariatur.</p>
      <p class="paragraph">Lorem ipsum dolor sit amet, consectetur adipisicing elit, sed do eiusmod tempor incididunt ut labore et dolore magna aliqua. Ut enim ad minim veniam, quis nostrud exercitation ullamco laboris nisi ut aliquip ex ea commodo consequat.</p>
      <p class="paragraph">Excepteur sint occaecat cupidatat non proident, sunt in culpa qui officia deserunt mollit anim id est laborum. re et dolore magnam aliquam quaerat voluptatem.</p>
      <div class="closing">
        <p>Regards</p>
        <p class="signature">Daniel Reyes</p>
      </div>
    </section>

    <footer class="footer-band" aria-hidden="true">
      <span class="band-orange"></span>
      <span class="band-gap"></span>
      <span class="band-blue"></span>
    </footer>
  </main>
</body>
</html>
```